Mayhon online ordering platform looking for a great web design

Mayhon - from the Vietnamese words Mây Hồng meaning financial success.
Background
Mayhon is an online ordering platform for small retail businesses (corner stores). The idea is that small retailers will use the website to order their supplies. From this we will utilise the group buying to get better deals for them that they could not achieve individually.
We are looking for a simple but stylish design for our ordering page. The layout needs to be efficient, logical and self explanatory.
Products to be sold on the site are FMCG (fast moving consumer goods). Potential to be 000's of items.
Considerations
- end users are not technologically adept.
- Users are generally older so small print will not be well received.
- Use of touch screen monitors to select/change items so spacing in design is vital.
- Logical display of category and sub-categories.
- Easy selection of products to order as well as modification of quantity.
- Shopping cart with easy change of item quantity.
- List of items for ordering can be paginated.
- Items listed will have image for easy identification.
- Search box
- Format should be in psd (photoshop) or complete html/css
- All this information needs to be displayed on the one page.
Product information to contain the following:
- Image
- Price
- Product name
- Size
Area for prominent display of specials without crowding the product information.

```html
<!DOCTYPE html>
<html lang="en">
<head>
<meta charset="utf-8">
<title>Mayhon – Sub Category</title>
<link href="https://fonts.googleapis.com/css2?family=Noto+Sans:wght@300;400;700&family=Oswald:wght@700&display=swap" rel="stylesheet">
<style>
:root{
  --orange:#f0562c;
  --orange-light:#f57a4c;
  --beige:#f4efe1;
  --beige-dark:#e9e1c9;
  --line:#dcd6c6;
  --text:#555;
  --dark:#222;
  --teal:#1bb8c4;
}
*{box-sizing:border-box;margin:0;padding:0}
html,body{width:960px;height:1200px;overflow:hidden;background:#fff;font-family:"Noto Sans",sans-serif;color:var(--text)}
.page{position:relative;width:960px;height:1200px}
.topbar{position:absolute;top:0;left:0;width:960px;height:11px;background:#0c0c0c}
.logo{position:absolute;left:103px;top:36px;font-size:25px;font-weight:300;color:#888;letter-spacing:.5px}

.main-nav{position:absolute;left:103px;top:92px;width:753px;height:27px;background:linear-gradient(#fbf8ef,var(--beige));border:1px solid var(--line);display:flex;align-items:center;font-size:10.5px}
.main-nav a{color:#555;text-decoration:none;height:100%;display:flex;align-items:center;justify-content:center;border-right:1px solid var(--line)}
.main-nav a.active{background:linear-gradient(var(--orange-light),var(--orange));color:#fff;font-weight:700;font-size:11.5px;width:80px;border:none;margin:-1px 0 -1px -1px;height:27px}
.main-nav .w1{width:79px}.main-nav .w2{width:81px}.main-nav .w3{width:99px}.main-nav .w4{width:94px}.main-nav .w5{width:76px}
.search{position:absolute;right:3px;top:3px;width:171px;height:20px;border:1px solid var(--line);background:#fff;font-size:10px;font-style:italic;color:#777;padding:3px 8px}

.hero{position:absolute;left:103px;top:124px;width:753px;height:155px;border:1px solid var(--line);background:#fff}
.banner{position:absolute;left:6px;top:5px;width:597px;height:144px;background:var(--teal);overflow:hidden}
.banner-photo{position:absolute;left:0;top:0;width:250px;height:144px;background:linear-gradient(90deg,#d9cfc4,#eee8e2 60%,var(--teal))}
.banner-upto{position:absolute;left:256px;top:40px;font-family:"Oswald",sans-serif;font-size:26px;color:#fff;transform:rotate(-90deg);transform-origin:left top;top:103px;left:258px;letter-spacing:1px}
.banner-offer{position:absolute;left:300px;top:12px;font-family:"Oswald",sans-serif;font-size:84px;line-height:110px;color:#fff;letter-spacing:1px}
.learn-more{position:absolute;right:5px;bottom:5px;width:96px;height:22px;background:#f7f3ea;border:1px solid var(--line);font-size:10.5px;color:#555;display:flex;align-items:center;justify-content:center}
.account{position:absolute;left:608px;top:5px;width:139px;height:144px;background:linear-gradient(var(--beige),#f8f4ea);border:1px solid #ece5d2;padding:9px 6px}
.welcome{font-size:12.5px;color:var(--dark)}
.account a{display:block;font-size:9.5px;color:var(--orange);text-decoration:none;line-height:11px}
.cart{position:absolute;left:6px;top:69px;width:130px;display:flex;justify-content:space-between}
.cart-label{font-size:12px;color:var(--dark)}
.cart-info{font-size:9px;color:var(--dark);line-height:11.5px;width:60px}
.cart-info em{color:var(--orange);font-size:8.5px}
.checkout{position:absolute;left:8px;bottom:5px;width:128px;height:17px;background:linear-gradient(var(--orange-light),var(--orange));border:1px solid #d8461e;color:#fff;font-size:9.5px;display:flex;align-items:center;justify-content:center}

.cat-bar{position:absolute;left:103px;width:753px;height:27px;background:linear-gradient(#fbf8ef,var(--beige));border:1px solid var(--line);display:flex;align-items:center;padding-left:6px;font-size:10.5px}
.cat-bar span{padding:0 8px;border-right:1px solid var(--line);line-height:15px;color:#555}
.cat-bar span.active{background:linear-gradient(var(--orange-light),var(--orange));color:#fff;font-weight:700;font-size:12px;line-height:27px;height:27px;margin:-1px 0;padding:0 7px;border:none}
.cat-main{top:284px}
.cat-sub{top:314px}

.breadcrumb{position:absolute;left:105px;top:352px;font-size:8.5px;color:#444}
.breadcrumb .current{color:var(--orange)}
.page-title{position:absolute;left:105px;top:364px;font-size:21px;font-weight:700;color:var(--orange);letter-spacing:.3px}

.section{position:absolute;left:104px;width:752px;border:1px solid var(--line);background:#fff}
.featured{top:400px;height:228px}
.latest{top:634px;height:600px}
.section-title{position:absolute;left:8px;top:7px;font-size:14px;color:var(--orange)}
.section-title small{font-size:9px;color:#555}
.rule{position:absolute;left:8px;width:730px;height:1px;background:var(--line)}

.product-row{position:absolute;left:9px;width:729px;height:180px;display:grid;grid-template-columns:135px 150px 149px 150px 145px}
.product{position:relative;border-right:1px solid #e4e0d6;height:100%}
.product:last-child{border-right:none}
.product .photo{position:absolute;top:0;left:50%;transform:translateX(-50%);width:52px;height:136px;border-radius:12px 12px 6px 6px}
.photo.green{background:linear-gradient(#46c23a,#2fa22a)}
.photo.blue{background:linear-gradient(#1d3f9e 0%,#f4f6fa 25%,#e9eef6)}
.photo.silver{background:linear-gradient(#f1f2f4,#d6dbe0)}
.photo.pink{background:linear-gradient(#e33c6a,#c3174b);width:40px}
.product .name{position:absolute;top:147px;left:18px;font-size:10.5px;color:var(--orange);font-weight:400}
.product .meta{position:absolute;top:162px;left:18px;right:14px;display:flex;justify-content:space-between;font-size:10px;color:#444}
</style>
</head>
<body>
<div class="page">
  <div class="topbar"></div>
  <div class="logo">LOGO HERE</div>

  <nav class="main-nav">
    <a class="active" href="#">Home</a>
    <a class="w1" href="#">About</a>
    <a class="w2" href="#">Categories</a>
    <a class="w3" href="#">How it works</a>
    <a class="w4" href="#">Contact Us</a>
    <a class="w5" href="#">Support</a>
    <div class="search">search</div>
  </nav>

  <section class="hero">
    <div class="banner">
      <div class="banner-photo" role="img" aria-label="Photo of a smiling shopper in a white top"></div>
      <div class="banner-upto">UPTO</div>
      <div class="banner-offer">20% OFF</div>
      <div class="learn-more">Learn More</div>
    </div>
    <aside class="account">
      <div class="welcome">Welcome, Minh</div>
      <a href="#">My Profile</a>
      <a href="#">Settings</a>
      <div class="cart">
        <span class="cart-label">My Cart</span>
        <div class="cart-info">4 Items<br><em>(Show Details)</em><br>$34,023</div>
      </div>
      <div class="checkout">Express Checkout</div>
    </aside>
  </section>

  <nav class="cat-bar cat-main">
    <span>Lorem</span><span>Ipsum</span><span>Proin</span><span>Gravida</span><span class="active">Main Category</span><span>Nibhvel</span><span>Auctor</span><span>Aliquet</span><span>Aenean</span>
  </nav>
  <nav class="cat-bar cat-sub">
    <span>Ipsum</span><span>Nec sagittis</span><span>Sem nibh id</span><span>Duis sed</span><span>Odio sit</span><span>Amet nibh</span><span class="active">Sub Category</span><span>Vulputate</span><span>Cursus</span><span>Amet</span>
  </nav>

  <div class="breadcrumb">Home &gt; Main Category &gt; <span class="current">Sub Category</span></div>
  <h1 class="page-title">Sub Category</h1>

  <section class="section featured">
    <h2 class="section-title">Featured Products</h2>
    <div class="rule" style="top:31px"></div>
    <div class="product-row" style="top:42px">
      <div class="product"><div class="photo green" role="img" aria-label="Green shampoo bottle"></div><div class="name">Product Name</div><div class="meta"><span>500ml</span><span>$2.59</span></div></div>
      <div class="product"><div class="photo blue" role="img" aria-label="White and blue shampoo bottle"></div><div class="name">Product Name</div><div class="meta"><span>500ml</span><span>$2.59</span></div></div>
      <div class="product"><div class="photo silver" role="img" aria-label="Silver shampoo bottle"></div><div class="name">Product Name</div><div class="meta"><span>500ml</span><span>$2.59</span></div></div>
      <div class="product"><div class="photo silver" role="img" aria-label="Silver shampoo bottle"></div><div class="name">Product Name</div><div class="meta"><span>500ml</span><span>$2.59</span></div></div>
      <div class="product"><div class="photo pink" role="img" aria-label="Pink shampoo bottle"></div><div class="name">Product Name</div><div class="meta"><span>500ml</span><span>$2.59</span></div></div>
    </div>
  </section>

  <section class="section latest">
    <h2 class="section-title">Latest Arrivals <small>(see all)</small></h2>
    <div class="rule" style="top:31px"></div>
    <div class="product-row" style="top:42px">
      <div class="product"><div class="photo green" role="img" aria-label="Green shampoo bottle"></div><div class="name">Product Name</div><div class="meta"><span>500ml</span><span>$2.59</span></div></div>
      <div class="product"><div class="photo blue" role="img" aria-label="White and blue shampoo bottle"></div><div class="name">Product Name</div><div class="meta"><span>500ml</span><span>$2.59</span></div></div>
      <div class="product"><div class="photo silver" role="img" aria-label="Silver shampoo bottle"></div><div class="name">Product Name</div><div class="meta"><span>500ml</span><span>$2.59</span></div></div>
      <div class="product"><div class="photo silver" role="img" aria-label="Silver shampoo bottle"></div><div class="name">Product Name</div><div class="meta"><span>500ml</span><span>$2.59</span></div></div>
      <div class="product"><div class="photo pink" role="img" aria-label="Pink shampoo bottle"></div><div class="name">Product Name</div><div class="meta"><span>500ml</span><span>$2.59</span></div></div>
    </div>
    <div class="rule" style="top:221px"></div>
    <div class="product-row" style="top:232px">
      <div class="product"><div class="photo green" role="img" aria-label="Green shampoo bottle"></div><div class="name">Product Name</div><div class="meta"><span>500ml</span><span>$2.59</span></div></div>
      <div class="product"><div class="photo blue" role="img" aria-label="White and blue shampoo bottle"></div><div class="name">Product Name</div><div class="meta"><span>500ml</span><span>$2.59</span></div></div>
      <div class="product"><div class="photo silver" role="img" aria-label="Silver shampoo bottle"></div><div class="name">Product Name</div><div class="meta"><span>500ml</span><span>$2.59</span></div></div>
      <div class="product"><div class="photo silver" role="img" aria-label="Silver shampoo bottle"></div><div class="name">Product Name</div><div class="meta"><span>500ml</span><span>$2.59</span></div></div>
      <div class="product"><div class="photo pink" role="img" aria-label="Pink shampoo bottle"></div><div class="name">Product Name</div><div class="meta"><span>500ml</span><span>$2.59</span></div></div>
    </div>
    <div class="rule" style="top:410px"></div>
    <div class="product-row" style="top:424px">
      <div class="product"><div class="photo green" role="img" aria-label="Green shampoo bottle"></div></div>
      <div class="product"><div class="photo blue" role="img" aria-label="White and blue shampoo bottle"></div></div>
      <div class="product"><div class="photo silver" role="img" aria-label="Silver shampoo bottle"></div></div>
      <div class="product"><div class="photo silver" role="img" aria-label="Silver shampoo bottle"></div></div>
      <div class="product"><div class="photo pink" role="img" aria-label="Pink shampoo bottle"></div></div>
    </div>
  </section>
</div>
</body>
</html>
```